"Velmora Crest" sexual performance enhancement pill bottle label needed.

This should be interesting...

I am starting a line of sexual performance enhancement products. This will be the first of several products basically. Keep in mind, I am the type of business person to stay with one company for years if they provide me with quality work.

This particular product is a male sexual performance pill. The name of the product is "Velmora Crest." The packaging of the pills are a black bottle with a white top. Label on the product example would be perfect but at a minimum I have attached a "template" for your guidance.

Some of the technical aspects of this are as follows:

-File Format: Illustrator CS6 is preferred. (Winner must provide artwork in layer and can not flatten artwork.)
-Resolution: 300 dpi minimum
-Bleed: 1/16th (0.0625") inch from edge of label
-Color Mode: CMYK only or must be converted to CMYK for final production

Lastly, this is your project as a designer, artist, creator, this is essentially a piece of you that will be sold and known by thousands of people. I have no color scheme that I prefer, just use the template and follow the layout. If you have any further questions, please feel free to contact me at any time.
Updates

Quick note on the product and what it does: -Powerful, long lasting, harder erections -Works in a minutes and last for hours -Enhances sexual desire and drive Thank you for your ideas...

Project Deadline Extended
Reason: We decided to extent the project for a few more days to let the last few concepts come in. So far things are looking really good and we definitely have seen some amazing designs. Thank you for your hard work and amazing creativity. Looking forward to seeing what we have come in the next couple of day. Very respectfully, Brev

ONLY THREE DAYS LEFT!!!! Please submit your ideas as soon as possible. And as always, thank you for your help!!! V/r, Brev

Industry/Entity Type

Graphic Design

```html
<!DOCTYPE html>
<html lang="en">
<head>
<meta charset="utf-8">
<title>Velmora Crest – Bottle Label</title>
<link href="https://fonts.googleapis.com/css2?family=Open+Sans:wght@400;600;700;800&family=PT+Sans+Narrow:wght@400;700&family=Montserrat:wght@700&display=swap" rel="stylesheet">
<style>
  :root{
    --page:#ffffff;
    --label-black:#050608;
    --ink:#ffffff;
    --royal:#1d3c78;
    --royal-light:#3d6fb4;
    --bronze:#a8582a;
    --gold:#f2d36a;
    --cream:#fff8dd;
    --smoke:#2a2d33;
  }
  *{margin:0;padding:0;box-sizing:border-box}
  html,body{width:1200px;height:1000px;overflow:hidden;background:var(--page)}
  .canvas{position:relative;width:1200px;height:1000px;background:var(--page)}
  .label{position:absolute;left:17px;top:41px;width:1161px;height:487px;background:var(--label-black);overflow:hidden;font-family:"Open Sans",Arial,sans-serif;color:var(--ink)}
  .backdrop-art{position:absolute;left:280px;top:0;width:620px;height:430px;
    background:radial-gradient(ellipse 160px 260px at 470px 230px, rgba(29,60,120,.85), rgba(29,60,120,0) 70%),
               radial-gradient(ellipse 200px 260px at 120px 200px, rgba(42,45,51,.75), rgba(42,45,51,0) 70%);}
  .directions{position:absolute;left:33px;top:30px;width:313px;font-size:9.3px;line-height:11.6px;text-align:justify}
  .directions p{margin-bottom:8px}
  .directions b{font-weight:800}
  .fda-note{position:absolute;left:35px;top:237px;width:311px;padding:4px 6px;font-size:8.6px;line-height:10.4px;font-weight:600;
    background:linear-gradient(90deg,var(--royal),var(--royal-light) 80%,var(--royal))}
  .maker{position:absolute;left:39px;top:300px;font-size:13.5px;line-height:18px;font-weight:700}
  .maker em{font-style:italic}
  .emblem{position:absolute;left:420px;top:10px;width:330px;height:350px}
  .claims{position:absolute;left:380px;top:372px;width:410px;text-align:center;font-family:"PT Sans Narrow",Arial,sans-serif;font-size:19px;line-height:27px}
  .facts{position:absolute;left:845px;top:38px;width:258px}
  .facts h2{font-family:Montserrat,Arial,sans-serif;font-size:28px;line-height:32px}
  .facts .serving{font-size:12.3px;font-weight:700;line-height:17px;margin-top:2px}
  .facts .rule-thick{height:5px;background:var(--royal);margin-top:4px}
  .facts .row-head{display:flex;justify-content:space-between;font-size:11px;padding:3px 2px;border-bottom:3px solid var(--royal)}
  .facts .blend{font-size:11px;line-height:15.2px;text-align:justify;padding:4px 0;border-bottom:5px solid var(--smoke)}
  .facts .blend b{font-weight:800}
  .facts .dv{font-size:12px;font-weight:700;margin-top:8px}
  .facts .other{font-size:10px;line-height:13.5px;margin-top:16px}
  .facts .other b{font-weight:800}
  .site{position:absolute;left:845px;top:360px;font-size:24px}
  .benefit-band{position:absolute;left:0;top:429px;width:100%;height:30px;
    background:linear-gradient(90deg,var(--royal) 0%,var(--royal) 70%,var(--royal-light) 88%,var(--royal) 100%);
    display:flex;justify-content:center;gap:34px;padding-left:20px;font-family:"PT Sans Narrow",Arial,sans-serif;font-size:19px;line-height:30px}
  .metal-band{position:absolute;left:0;top:459px;width:100%;height:28px;
    background:linear-gradient(90deg,var(--bronze) 0%,var(--bronze) 30%,var(--gold) 50%,var(--cream) 70%,var(--gold) 100%)}
</style>
</head>
<body>
<div class="canvas">
  <section class="label">
    <div class="backdrop-art" role="img" aria-label="Soft silhouette of a woman and flowing swirl shapes in blue and grey"></div>

    <div class="directions">
      <p><b>SUGGESTED USE:</b> As a dietary supplement, take two (2) capsules 1 hour before physical activity, or as directed by your health care professional. Do not exceed two (2) capsules daily.</p>
      <p><b>CAUTION:</b> Do not exceed recommended dose. This product is not intended for pregnant or nursing mothers, children under the age of 18, or individuals taking prescription drugs. Discontinue use immediately if nausea, sleeplessness, nervousness occur. Do not take this product if you have a known medical condition including high blood pressure, diabetes, any cardiovascular disorder, heart disease, hyperthyroidism or are taking anti-depressant medication. If you have questions about the advisability of taking this product consult your physician prior to use.</p>
      <p><b>KEEP OUT OF THE REACH OF CHILDREN. DO NOT USE IF SAFETY SEAL IS DAMAGED OR MISSING. STORE AT ROOM TEMPERATURE.</b></p>
    </div>
    <div class="fda-note">* These statements have not been evaluated by the Food and Drug Administration. This product is not intended to diagnose, treat, cure or prevent any disease.</div>
    <div class="maker"><em>Manufactured Exclusively For:</em><br>COMPANY INFO</div>

    <svg class="emblem" viewBox="0 0 330 350" aria-label="Velmora Crest">
      <defs><path id="arc" d="M40 150 A125 125 0 0 1 290 150"/></defs>
      <text font-family="Open Sans, Arial, sans-serif" font-size="27" font-weight="700" fill="#ffffff" text-anchor="middle">
        <textPath href="#arc" startOffset="50%">MALE ENHANCEMENT</textPath>
      </text>
      <circle cx="165" cy="200" r="82" fill="#1d3c78"/>
      <text x="165" y="330" font-family="Open Sans, Arial, sans-serif" font-size="38" font-weight="700" fill="#ffffff" text-anchor="middle">Velmora Crest</text>
    </svg>

    <div class="claims">Works in a minutes and last for hours<br>Enhances Sexual Desire and Drive</div>

    <div class="facts">
      <h2>Supplement Facts</h2>
      <div class="serving">Serving Size: 2 Capsules<br>Servings Per Container: 30</div>
      <div class="rule-thick"></div>
      <div class="row-head"><span>Amount Per Serving</span><span>% Daily Value</span></div>
      <div class="blend"><b>VCR-Rx™ Proprietary Formula 1,560 mg †</b> Horny Goat Weed (herb powder), Maca (herb powder), Mucuna Pruriens (L-Dopa), Polypodium Vulgare (herb powder), Yohimbe Bark (herb powder), Saw Palmetto (herb powder), Muira Puama (herb powder), Arginine (L-Arginine hydrochloride), Panax Ginseng (herb powder)</div>
      <div class="dv">† % Daily Value not established</div>
      <div class="other"><b>Other Ingredients:</b> Gelatin, Magnesium Stearate, and Calcium Carbonate.</div>
    </div>
    <div class="site">www.VelmoraCrestPill.com</div>

    <div class="benefit-band"><span>Powerful</span><span>Long Lasting</span><span>Harder Erections</span></div>
    <div class="metal-band"></div>
  </section>
</div>
</body>
</html>
```